ultra-minimalist business card

front (black background, matte):

reza t. kovin
writer | photographer
get@rezakovin.com

back (white background, matte):

a picture speaks a thousand words;
a word draws a thousand pictures.

www.rezakovin.com

all text should be small (white or silver - as long as it shows against the black - on the front; black or gray - as long as it shows against the white - on the back).

feel free to get creative in terms of arrangement, alignment, and font type, but remember, the overall style is minimalist, so nothing too fancy, please.

thanks.

```html
<!DOCTYPE html>
<html lang="en">
<head>
<meta charset="utf-8">
<title>Reza T. Kovin — Business Card</title>
<link rel="stylesheet" href="https://fonts.googleapis.com/css2?family=Mulish:ital,wght@0,300;0,400;0,800;1,300&display=swap">
<style>
  :root {
    --backdrop: #e4e4e6;
    --paper-white: #f4f4f4;
    --quote-gray: #8e8e8e;
    --mark-gray: #a3a3a3;
    --url-gray: #9a9a9a;
    --card-dark-top: #6c6c6c;
    --card-dark-bottom: #111111;
    --silver: #c9c9c9;
    --silver-dim: #9d9d9d;
  }
  * { box-sizing: border-box; margin: 0; padding: 0; }
  html, body {
    width: 1200px; height: 720px; overflow: hidden;
    background: var(--backdrop);
    font-family: "Mulish", sans-serif;
  }
  .stage {
    position: relative; width: 1200px; height: 720px;
  }
  .card {
    position: absolute; top: 210px;
    width: 520px; height: 300px;
  }
  /* back side */
  .card-back {
    left: 50px;
    background: var(--paper-white);
  }
  .quote {
    position: absolute; left: 78px; top: 74px;
    font-style: italic; font-weight: 300;
    font-size: 25px; line-height: 34px;
    color: var(--quote-gray);
    letter-spacing: 0.2px;
  }
  .quote-line { display: block; white-space: nowrap; }
  .quote-line-second { padding-left: 22px; }
  .quote-mark {
    position: absolute;
    font-family: "Mulish", sans-serif;
    font-weight: 800; font-style: normal;
    font-size: 78px; line-height: 1;
    color: var(--mark-gray);
  }
  .quote-mark-open { left: 30px; top: 70px; }
  .quote-mark-close { left: 446px; top: 36px; }
  .divider {
    position: absolute; left: 246px; top: 172px;
    width: 28px; height: 2px; background: var(--quote-gray);
  }
  .website {
    position: absolute; left: 0; right: 0; top: 186px;
    text-align: center;
    font-size: 13px; font-weight: 400; letter-spacing: 1px;
    color: var(--url-gray);
  }
  /* front side */
  .card-front {
    left: 630px;
    background: linear-gradient(205deg, var(--card-dark-top) 0%, #3a3a3a 45%, var(--card-dark-bottom) 100%);
  }
  .identity {
    position: absolute; left: 34px; bottom: 40px;
  }
  .name {
    font-size: 26px; font-weight: 300; letter-spacing: 2.5px;
    color: var(--silver); text-transform: uppercase; line-height: 1;
  }
  .role {
    margin-top: 4px;
    font-size: 13px; font-weight: 300; letter-spacing: 1px;
    color: var(--silver-dim);
  }
  .email {
    position: absolute; right: 22px; bottom: 42px;
    font-size: 13px; font-weight: 300; letter-spacing: 0.8px;
    color: var(--silver-dim);
  }
</style>
</head>
<body>
  <main class="stage">
    <section class="card card-back" aria-label="Card back">
      <span class="quote-mark quote-mark-open" aria-hidden="true">“</span>
      <p class="quote">
        <span class="quote-line">a picture speaks a thousand words,</span>
        <span class="quote-line quote-line-second">a word draws a thousand pictures.</span>
      </p>
      <span class="quote-mark quote-mark-close" aria-hidden="true">”</span>
      <span class="divider" aria-hidden="true"></span>
      <p class="website">www.rezakovin.com</p>
    </section>

    <section class="card card-front" aria-label="Card front">
      <div class="identity">
        <h1 class="name">Reza T. Kovin</h1>
        <p class="role">writer | photographer</p>
      </div>
      <p class="email">get@rezakovin.com</p>
    </section>
  </main>
</body>
</html>
```